VORNAK SYSTEMS BUSINESS CARD DESIGN

WE WANT COMPLETE NEW DESIGN OF OUR BUSINESS CARD. WE ARE AN INTEGRATION COMPANY, WHERE WE INTEGRATE IOT/SMART SYSTEMS TO HOMES AND CORPORATE CUSTOMERS. WE SUPPLY AND INSTALL AUTOMATION PRODUCTS. THE FINAL DESIGN SHOULD COMMUNICATE TECHNOLOGY. THE CARD DESIGN SHOULD BE VERY IMPACT FULL. LOGO NEEDS TO BE THERE. IT WOULD NICE IF THE DESIGN WAS CLEAN. COLORS IS UP TO DESIGNER TO PLAY WITH, OR CAN STICK TO CORPORATE COLORS (FOLLOW LOGO). I HAVE ADDED FEW REFERENCE PHOTOS TO DRAW INSPIRATION MAYBE. I HAVE ADDED A HEX DESIGN, ITS NOT NECESSARY TO USE THIS DESIGN, ITS UPTO DESIGNER, JUST ADDED IF NEEDED TO PLAY WITH DESIGN.

Target Market(s)

Private end users and corporate clients

Industry/Entity Type

technology, home automation, home theaters, building management systems, IOT

Contact Information for Business Card

It should include Employee name, personal number, office number, email address, both in English and arabic. DETAILS TO INCLUDE :RAJESH PALLIVAL, MOBILE 0097150738265,OFFCIE 009714368547, RAJESH@VORNAKSYS.EXAMPLE

Requirements
Must have
• Should feel like a technology company from design. Details both and in English and arabic (or at least have provision for arabic in design).
Nice to have
• I would like logo on one side, and details on the other side. Logo design side should communicate technology with logo. Other side can be clean just with information or also have some design aspects following from logo side. it would be interesting to see submissions with square design as well (that looks like an app Icon). colors could be of logo, red black grey and white. I have added some designs to draw inspiration from

```html
<!DOCTYPE html>
<html lang="en">
<head>
<meta charset="utf-8">
<title>Vornak Systems — Business Card</title>
<link href="https://fonts.googleapis.com/css2?family=Arimo:wght@400;700&family=Michroma&display=swap" rel="stylesheet">
<style>
  :root {
    --stage: #121212;
    --card: #2c2c2e;
    --card-edge: #353537;
    --white: #f4f4f4;
    --grey: #a9a9ab;
    --grey-dark: #6d6d70;
    --red: #e21b23;
    --sheen-dark: #1c1c1e;
    --sheen-light: #5a5a5d;
  }
  * { box-sizing: border-box; margin: 0; padding: 0; }
  html, body { width: 1200px; height: 963px; overflow: hidden; background: var(--stage); }
  .stage {
    width: 1200px; height: 963px;
    display: flex; flex-direction: column; align-items: center; justify-content: center; gap: 46px;
  }
  .card {
    position: relative; width: 720px; height: 411px;
    background: var(--card); border: 1px solid var(--card-edge);
    box-shadow: 0 14px 40px rgba(0,0,0,.6);
    overflow: hidden;
  }

  /* front: brand + details */
  .brand {
    position: absolute; top: 92px; left: 0; right: 0;
    display: flex; flex-direction: column; align-items: center;
  }
  .brand-lockup { display: flex; align-items: center; gap: 16px; }
  .brand-dot { width: 34px; height: 34px; border-radius: 50%; background: var(--red); }
  .brand-name {
    font-family: "Michroma", sans-serif; font-size: 38px; color: var(--white);
    letter-spacing: 2px;
  }
  .brand-tagline {
    margin-top: 14px;
    font-family: "Michroma", sans-serif; font-size: 14px; color: var(--white);
    letter-spacing: 5px;
  }

  .person {
    position: absolute; top: 262px; left: 92px; text-align: right; width: 200px;
    font-family: "Arimo", sans-serif;
  }
  .person-name { font-size: 19px; font-weight: 700; color: var(--red); letter-spacing: .3px; }
  .person-role { margin-top: 6px; font-size: 16px; color: var(--grey); }

  .divider {
    position: absolute; left: 310px; top: 258px; width: 1px; height: 82px; background: var(--grey-dark);
  }

  .contacts {
    position: absolute; left: 330px; top: 262px; list-style: none;
    font-family: "Arimo", sans-serif; font-size: 16px; color: var(--white); letter-spacing: .3px;
  }
  .contacts li { display: flex; align-items: center; gap: 10px; height: 26px; }
  .contacts svg { width: 16px; height: 16px; flex: none; }

  /* back: brand panel */
  .card-back {
    background: linear-gradient(160deg, var(--card) 0%, var(--sheen-dark) 45%, var(--sheen-light) 78%, var(--sheen-dark) 100%);
  }
  .back-mark {
    position: absolute; inset: 0;
    display: flex; align-items: center; justify-content: center; gap: 22px;
  }
  .back-mark .brand-dot { width: 52px; height: 52px; background: var(--grey-dark); }
  .back-mark .brand-name { font-size: 46px; color: #4a4a4d; }
</style>
</head>
<body>
<main class="stage">

  <section class="card card-front" aria-label="Business card, details side">
    <div class="brand">
      <div class="brand-lockup">
        <span class="brand-dot"></span>
        <span class="brand-name">VORNAK SYSTEMS</span>
      </div>
      <p class="brand-tagline">A VORNAK GROUP DIVISION.</p>
    </div>

    <div class="person">
      <p class="person-name">RAJESH PALLIVAL</p>
      <p class="person-role">General Manager</p>
    </div>

    <span class="divider"></span>

    <ul class="contacts">
      <li>
        <svg viewBox="0 0 16 16" aria-hidden="true"><rect x="4" y="1" width="8" height="14" rx="1.5" fill="none" stroke="#e21b23" stroke-width="1.5"/><line x1="7" y1="12.5" x2="9" y2="12.5" stroke="#e21b23" stroke-width="1.5"/></svg>
        0097150738265
      </li>
      <li>
        <svg viewBox="0 0 16 16" aria-hidden="true"><path d="M3 2 L6 2 L7 5.5 L5.3 6.8 C6.2 8.8 7.4 10 9.3 10.8 L10.6 9.1 L14 10 L14 13 C14 13.6 13.5 14 13 14 C7.5 13.6 2.4 8.5 2 3 C2 2.5 2.4 2 3 2 Z" fill="#e21b23"/></svg>
        009714368547
      </li>
      <li>
        <svg viewBox="0 0 16 16" aria-hidden="true"><rect x="1.5" y="3.5" width="13" height="9" fill="none" stroke="#e21b23" stroke-width="1.5"/><polyline points="1.5,3.5 8,9 14.5,3.5" fill="none" stroke="#e21b23" stroke-width="1.5"/></svg>
        RAJESH@VORNAKSYS.EXAMPLE
      </li>
    </ul>
  </section>

  <section class="card card-back" aria-label="Business card, brand side">
    <div class="back-mark">
      <span class="brand-dot"></span>
      <span class="brand-name">VORNAK SYSTEMS</span>
    </div>
  </section>

</main>
</body>
</html>
```